Business Card for Multi-Brand Sportswear Company

We are looking for a business card which represents our company and the multiple brands within it.

The company: Fen Athletics (LTD)
The brands: Fen, TavaPuni, ElmStretch, Grit and Rain

Employees using these cards would be representing Fen Athletics, rather than any of the individual brands. You will see a current design within the uploaded files, to give some inspiration. The actual text of the brands is not necessary, but the logos should be on there is some format.

Our creative minds on this are stretched, so we are looking for someone to make this their own, and show us what a good business card should look like.

We may like to get these printed with spot gloss, so keep that in mind with your designs.

www.fenathletics.co.uk

Industry/Entity Type

Business

Contact Information for Business Card

Leo Pemberton-Hale
Operations Manager
(+44) 1632 960 418
Leo@fenathletics.co.uk
www.fenathletics.co.uk

Font styles to use
Sans Serif
Other font styles liked:
• Eurostile

Colors
ffffff

Requirements
Nice to have
• Dark (black) background

```html
<!DOCTYPE html>
<html lang="en">
<head>
<meta charset="utf-8">
<title>Fen Athletics – Business Card</title>
<link href="https://fonts.googleapis.com/css2?family=Open+Sans:wght@400;600;700&display=swap" rel="stylesheet">
<style>
  :root {
    --stage: #4a4a4a;
    --card-front-top: #2c2c2c;
    --card-front-bottom: #1f1f1f;
    --card-back: #050505;
    --red: #e5383b;
    --white: #ffffff;
    --light: #e6e6e6;
    --silver: #bdbdbd;
    --ghost: rgba(255,255,255,0.05);
    --badge: #5b4a5e;
  }
  * { margin: 0; padding: 0; box-sizing: border-box; }
  html, body { width: 1200px; height: 900px; overflow: hidden; }
  body {
    background: var(--stage);
    font-family: "Open Sans", Arial, sans-serif;
    position: relative;
  }
  .card {
    position: absolute;
    top: 271px;
    width: 457px;
    height: 281px;
    border-radius: 14px;
    overflow: hidden;
  }
  .card--front {
    left: 137px;
    background: linear-gradient(180deg, var(--card-front-top), var(--card-front-bottom));
  }
  .card--back { left: 626px; background: var(--card-back); }

  .wordmark { position: absolute; color: var(--red); font-weight: 700; letter-spacing: 0.5px; line-height: 1; }
  .card--front .wordmark { left: 24px; top: 34px; font-size: 24px; }
  .tagline {
    display: block; font-weight: 400; font-size: 5.5px; letter-spacing: 1.2px;
    margin-top: 4px; margin-left: 140px; color: var(--red);
  }
  .watermark {
    position: absolute; right: -10px; bottom: -30px;
    font-size: 170px; font-weight: 700; color: var(--ghost); line-height: 1;
    letter-spacing: -4px;
  }
  .holder { position: absolute; right: 18px; top: 20px; text-align: right; }
  .holder__name { color: var(--red); font-weight: 700; font-size: 14px; letter-spacing: 0.2px; }
  .holder__role { color: var(--light); font-size: 12px; margin-top: 1px; }

  .address { position: absolute; left: 23px; top: 165px; color: var(--light); font-size: 12px; line-height: 18px; }
  .address strong { font-weight: 600; color: var(--white); }
  .contacts { position: absolute; left: 23px; top: 215px; list-style: none; color: var(--light); font-size: 12px; line-height: 17px; }
  .contacts li { display: flex; align-items: center; gap: 6px; }
  .contacts svg { width: 9px; height: 9px; fill: var(--red); }

  .card--back .wordmark {
    left: 0; right: 0; top: 110px; text-align: center; color: var(--silver);
    font-size: 34px; font-weight: 600;
  }
  .card--back .tagline { color: var(--silver); font-size: 8.5px; letter-spacing: 1.5px; margin-left: 170px; margin-top: 6px; }
  .brand-row {
    position: absolute; left: 0; right: 0; top: 229px;
    display: flex; justify-content: center; align-items: center; gap: 24px;
    list-style: none; font-size: 9px; font-weight: 600; color: var(--silver);
  }
  .brand-row .dot { display: inline-block; width: 8px; height: 8px; border-radius: 50%; background: var(--badge); margin-right: 4px; vertical-align: middle; }
</style>
</head>
<body>
  <section class="card card--front">
    <div class="watermark" aria-hidden="true">Fen</div>
    <div class="wordmark">Fen Athletics<span class="tagline">PERFORMANCE WEAR</span></div>
    <div class="holder">
      <div class="holder__name">OWEN HARDCASTLE</div>
      <div class="holder__role">MANAGING DIRECTOR</div>
    </div>
    <address class="address" style="font-style:normal">
      <strong>Marsh Court,</strong><br>
      Elmby,Wexton,ZZ1 4QT
    </address>
    <ul class="contacts">
      <li><svg viewBox="0 0 10 10"><path d="M1 3c0-1 1-2 2-2h4c1 0 2 1 2 2v1H7V3H3v1H1zM2 5h6l1 4H1z"/></svg>+44(0)1632 960418</li>
      <li><svg viewBox="0 0 10 10"><path d="M1 2h8v6H1zM1.5 2.5 5 5.5l3.5-3"/></svg>owen@fenathletics.co.uk</li>
      <li><svg viewBox="0 0 10 10"><circle cx="5" cy="5" r="4.5"/></svg>www.fenathletics.co.uk</li>
    </ul>
  </section>

  <section class="card card--back">
    <div class="wordmark">Fen Athletics<span class="tagline">PERFORMANCE WEAR</span></div>
    <ul class="brand-row">
      <li>Fen</li>
      <li>TavaPuni</li>
      <li><span class="dot"></span>ElmStretch</li>
      <li>Grit and Rain</li>
    </ul>
  </section>
</body>
</html>
```